Valmora Health a direct primary care practice needs a beautiful and customer friendly website

We need a website to showcase our new medical practice. We want to enhance the customer experience and make it easy to navigate to the desired page by placing pillar pages on the home screen. the website needs to be clean and bright.

Target Market(s)

Uninsured, Small businesses that can't afford to offer employees insurance.

Industry/Entity Type

Healthcare

Coding

Coded - Design and coding required

Font styles to use
Serif
Sans Serif

Colors
0592cd
3377b5
0355a3
9bcb3c
acd136

Requirements
Must have
• Must be user friendly, must have pillar pages to help boost SEO ranking, clean and bright, must be close to the in colors to the attached logo.

Content will be very similar to www.quillbrookhealth.example
Nice to have
• Clean and easy to read font

```html
<!DOCTYPE html>
<html lang="en">
<head>
<meta charset="utf-8">
<title>Valmora Health – Healthcare Reimagined</title>
<link rel="stylesheet" href="https://fonts.googleapis.com/css2?family=Cinzel:wght@400;600;700&family=Poppins:ital,wght@0,300;0,400;0,500;0,600;1,300;1,400&display=swap">
<style>
:root{
  --navy:#1b2f9e;
  --band:#1a33a1;
  --deep:#03073b;
  --green:#0c8f3b;
  --text:#333845;
  --muted:#555b66;
  --line:#e8e9ee;
  --white:#ffffff;
}
*{margin:0;padding:0;box-sizing:border-box}
html,body{width:1200px;height:2719px;overflow:hidden}
body{position:relative;background:var(--white);font-family:'Poppins',sans-serif;color:var(--text)}
.abs{position:absolute}

/* header */
.site-header{left:0;top:0;width:1200px;height:75px;background:var(--white)}
.brand{left:60px;top:22px;font-family:'Cinzel',serif;font-size:26px;font-weight:400;color:var(--navy);letter-spacing:.5px}
.nav{left:559px;top:31px;display:flex;font-size:11px;color:#333}
.nav a{color:#333;text-decoration:none;margin-right:22px;text-transform:uppercase}
.nav a.active{color:var(--navy);position:relative}
.nav a.active::before{content:"";position:absolute;left:-6px;right:-6px;top:-31px;height:3px;background:var(--navy)}
.btn-join{left:1050px;top:19px;width:90px;height:36px;background:var(--green);color:#fff;border-radius:3px;font-family:'Cinzel',serif;font-size:13px;font-weight:600;display:flex;align-items:center;justify-content:center;letter-spacing:.5px}

/* hero */
.hero-photo{left:0;top:75px;width:1200px;height:598px;background:linear-gradient(90deg,#e6e7e9 0%,#dcdddf 40%,#c9b9ad 62%,#e8e4df 80%,#d5d8dc 100%)}
.hero-eyebrow{left:106px;top:256px;font-size:15px;color:var(--green);letter-spacing:2.5px}
.hero-title{left:104px;top:284px;font-family:'Cinzel',serif;font-weight:700;font-size:44px;line-height:50px;color:var(--deep)}
.hero-title .accent{color:var(--navy)}
.hero-sub{left:106px;top:444px;font-size:15px;color:#222}
.btn{height:40px;border-radius:3px;font-family:'Cinzel',serif;font-size:15px;font-weight:600;display:flex;align-items:center;justify-content:center;letter-spacing:.5px}
.btn-book{left:104px;top:477px;width:214px;background:var(--green);color:#fff}
.btn-contact{left:325px;top:477px;width:145px;background:#fff;color:#111;border:1px solid #333}
.slide-arrow{top:367px;width:38px;height:37px;background:#fff;border-radius:2px;display:flex;align-items:center;justify-content:center}

/* emergency band */
.emergency{left:0;top:673px;width:1200px;height:76px;background:var(--band);color:#fff}
.emergency-text{left:224px;top:28px;font-size:15px}
.emergency-icon{left:720px;top:16px}
.emergency-phone{left:778px;top:20px;font-family:'Cinzel',serif;font-size:24px;letter-spacing:.5px}

/* welcome */
.welcome-eyebrow{left:121px;top:820px;font-family:'Cinzel',serif;font-size:15px;color:var(--green)}
.welcome-title{left:119px;top:842px;font-family:'Cinzel',serif;font-size:37px;font-weight:600;color:var(--navy)}
.welcome-block{left:0;top:1113px;width:366px;height:187px;background:var(--deep)}
.welcome-photo{left:120px;top:927px;width:390px;height:299px;background:linear-gradient(120deg,#e9e8e4 0%,#c8b6a6 40%,#9fb2c6 70%,#2f64b4 100%)}
.welcome-lead{left:583px;top:865px;width:300px;font-size:14px;line-height:21px;color:var(--navy)}
.welcome-copy{left:583px;top:923px;width:430px;font-size:11.5px;line-height:21px;color:var(--muted)}
.welcome-copy p{margin-bottom:14px}
.checklist{left:583px;top:1106px;list-style:none;font-size:12.5px;color:#333}
.checklist li{display:flex;align-items:center;height:32.5px}
.checklist svg{margin-right:18px}

/* cards */
.card{top:1375px;width:304px;height:232px;background:#fff;border:1px solid var(--line);border-right:4px solid var(--line);border-bottom:4px solid var(--line);padding:42px 30px 0}
.card.featured{border:1px solid var(--navy);border-right:4px solid var(--navy);border-bottom:4px solid var(--navy)}
.card h3{font-family:'Cinzel',serif;font-size:18px;font-weight:600;color:var(--deep);margin-bottom:10px}
.card p{font-size:11.5px;line-height:20px;color:var(--muted)}
.card .action{position:absolute;left:26px;top:162px;display:flex;align-items:center;gap:12px;font-size:13px;font-weight:600;color:var(--navy);text-transform:uppercase}
.card .closed{color:var(--green);font-weight:600;text-decoration:underline}

.divider{left:58px;top:1682px;width:1082px;height:1px;background:var(--line)}

/* patients */
.patients-title{left:320px;top:1752px;font-family:'Cinzel',serif;font-size:37px;font-weight:600;color:var(--navy)}
.patients-rule{left:618px;top:1738px;width:1px;height:92px;background:var(--line)}
.rating{left:646px;top:1736px}
.rating-label{left:655px;top:1756px;width:74px;text-align:center;font-size:10px;color:#333}
.rating-value{left:655px;top:1770px;width:70px;text-align:center;font-size:23px;font-weight:600;color:var(--deep)}
.stars{left:774px;top:1762px}
.quote{left:290px;top:1877px;width:620px;text-align:center;font-size:14.5px;font-style:italic;font-weight:300;line-height:27px;color:#222}
.client{left:0;top:1980px;width:1200px;text-align:center;font-family:'Cinzel',serif;font-size:15px;color:var(--navy)}
.dots{left:556px;top:2021px;display:flex;gap:9px}
.dots span{width:10px;height:10px;border-radius:50%;background:#dcdee6}
.dots span.on{background:var(--deep)}

/* contact */
.contact-title{left:130px;top:2176px;font-family:'Cinzel',serif;font-size:37px;font-weight:600;color:var(--navy)}
.contact-item{left:131px;display:flex;gap:14px;font-size:12px;line-height:17px;color:#333}
.contact-icon{width:38px;height:38px;border-radius:8px;background:var(--navy);display:flex;align-items:center;justify-content:center;flex-shrink:0}
.map{left:447px;top:2111px;width:753px;height:398px;background:linear-gradient(135deg,#eeeeee 0%,#e4e4e4 50%,#ececec 100%)}
.map-edge{left:1181px;top:2171px;width:19px;height:293px;background:var(--band)}

/* footer */
.site-footer{left:0;top:2509px;width:1200px;height:210px;background:var(--band);color:#fff}
.footer-brand{left:60px;top:96px;font-family:'Cinzel',serif;font-size:28px;font-weight:400;color:#fff}
.social{top:59px;width:37px;height:37px;border:1px solid rgba(255,255,255,.7);border-radius:50%}
.footer-links{right:62px;top:114px;font-size:12px;color:#fff;display:flex;gap:12px}
.footer-copy{right:62px;top:136px;font-size:12px;color:#fff}
</style>
</head>
<body>

<header class="abs site-header">
  <div class="abs brand">Valmora Health</div>
  <nav class="abs nav">
    <a class="active">Home</a><a>About</a><a>Services</a><a>Employers</a><a>Pricing</a><a>Contact Us</a><a>Blog</a>
  </nav>
  <div class="abs btn-join">JOIN US</div>
</header>

<section>
  <div class="abs hero-photo" role="img" aria-label="Photo of a doctor talking with a smiling senior patient in a bright clinic"></div>
  <div class="abs slide-arrow" style="left:42px"><svg width="12" height="18" viewBox="0 0 12 18"><path d="M10 1 2 9l8 8" fill="none" stroke="#888" stroke-width="1.5"/></svg></div>
  <div class="abs slide-arrow" style="left:1121px"><svg width="12" height="18" viewBox="0 0 12 18"><path d="m2 1 8 8-8 8" fill="none" stroke="#888" stroke-width="1.5"/></svg></div>
  <div class="abs hero-eyebrow">HEALTHCARE REIMAGINED</div>
  <h1 class="abs hero-title">WE TAKE CARE<br>OF YOUR<br><span class="accent">HEALTH NOW</span></h1>
  <p class="abs hero-sub">Improving the Quality Of Your Life Through Better Health.</p>
  <div class="abs btn btn-book">BOOK APPOINTMENT</div>
  <div class="abs btn btn-contact">CONTACT US</div>
</section>

<section class="abs emergency">
  <div class="abs emergency-text">Need a Doctor for Check-up? Call for an Emaergency Services</div>
  <svg class="abs emergency-icon" width="44" height="44" viewBox="0 0 44 44">
    <circle cx="22" cy="22" r="20" fill="none" stroke="#fff" stroke-width="1.5"/>
    <circle cx="24" cy="20" r="10" fill="#fff"/>
    <path d="M21 13h6v4h4v6h-4v4h-6v-4h-4v-6h4z" fill="var(--green)"/>
    <path d="M9 15c-2 6 3 16 11 20l3-4-4-3-2 2c-3-2-5-5-6-8l2-2-3-4z" fill="none" stroke="#fff" stroke-width="1.5"/>
  </svg>
  <div class="abs emergency-phone">+1 (555) 014 2236</div>
</section>

<section>
  <div class="abs welcome-eyebrow">Welcome To</div>
  <h2 class="abs welcome-title">Valmora Health</h2>
  <div class="abs welcome-block"></div>
  <div class="abs welcome-photo" role="img" aria-label="Photo of a smiling patient with a nurse in blue scrubs"></div>
  <p class="abs welcome-lead">Improving the Quality Of Your Life Through Better Health.</p>
  <div class="abs welcome-copy">
    <p>Lorem Ipsum has been the industry's standard dummy text ever since the 1500s, when an unknown printer took a galley of type and scrambled it to make a type specimen book text print industry text.</p>
    <p>Lorem Ipsum has been the industry's standard dummy text ever since the 1500s, when an unknown printer took a galley of type and scrambled it to make a type specimen book. It has survived not only five centuries, but also the leap into electronic typesetting, remaining.</p>
  </div>
  <ul class="abs checklist">
    <li><svg width="18" height="14" viewBox="0 0 18 14"><path d="M1 7l5 5L17 1" fill="none" stroke="var(--green)" stroke-width="2.5"/></svg>Lorem Ipsum has been the industry</li>
    <li><svg width="18" height="14" viewBox="0 0 18 14"><path d="M1 7l5 5L17 1" fill="none" stroke="var(--green)" stroke-width="2.5"/></svg>Lorem Ipsum has been the industry</li>
    <li><svg width="18" height="14" viewBox="0 0 18 14"><path d="M1 7l5 5L17 1" fill="none" stroke="var(--green)" stroke-width="2.5"/></svg>Lorem Ipsum has been the industry</li>
    <li><svg width="18" height="14" viewBox="0 0 18 14"><path d="M1 7l5 5L17 1" fill="none" stroke="var(--green)" stroke-width="2.5"/></svg>Lorem Ipsum has been the industry</li>
  </ul>
</section>

<section>
  <article class="abs card" style="left:120px">
    <h3>Benefits</h3>
    <p>We offer unlimited office visits and personal Communications via phone, secure e-mail and text.</p>
    <div class="action">
      <svg width="52" height="46" viewBox="0 0 52 46"><circle cx="16" cy="7" r="5" fill="none" stroke="var(--navy)" stroke-width="2"/><path d="M6 44V26c0-8 20-8 20 0v18M12 44V32M20 44V32" fill="none" stroke="var(--navy)" stroke-width="2"/><path d="M32 18h6v-6h6v6h6v6h-6v6h-6v-6h-6z" fill="#2d55d8"/></svg>
      Learn More
    </div>
  </article>
  <article class="abs card featured" style="left:447px">
    <h3>Question?</h3>
    <p>How dose this work? What about insurance? Do you work with Silverline Care? Here are some answers.</p>
    <div class="action">
      <svg width="32" height="46" viewBox="0 0 32 46"><path d="M5 14C5 6 11 2 17 2s12 4 12 11-9 9-9 16v4" fill="none" stroke="var(--navy)" stroke-width="3"/><circle cx="20" cy="41" r="3" fill="var(--navy)"/></svg>
      Contact Us
    </div>
  </article>
  <article class="abs card" style="left:775px">
    <h3>Office Hours</h3>
    <p>Mon- Fri : 9:00 Am -6:00 Pm<br>Saturday : 9:00 Am - 3:00 Pm<br>Sunday : <span class="closed">Closed</span></p>
    <div class="action">
      <svg width="46" height="46" viewBox="0 0 46 46"><circle cx="23" cy="22" r="20" fill="none" stroke="var(--navy)" stroke-width="2"/><circle cx="23" cy="22" r="14" fill="#2d55d8"/><path d="M23 13v9l6 4" fill="none" stroke="#fff" stroke-width="2"/><path d="M6 36l-4 8 9-4" fill="none" stroke="var(--navy)" stroke-width="2"/></svg>
      Book an Apointment
    </div>
  </article>
</section>

<div class="abs divider"></div>

<section>
  <h2 class="abs patients-title">Our Patients</h2>
  <div class="abs patients-rule"></div>
  <svg class="abs rating" width="110" height="96" viewBox="0 0 110 96">
    <path d="M55 4C25 4 4 20 4 40s18 34 38 36c6 0 10 4 14 12 2-8 6-12 10-13 20-4 38-17 38-35S85 4 55 4z" fill="none" stroke="#d8e6f3" stroke-width="3"/>
  </svg>
  <div class="abs rating-label">Overall Rating</div>
  <div class="abs rating-value">4.5</div>
  <svg class="abs stars" width="106" height="20" viewBox="0 0 106 20" fill="var(--green)">
    <path id="st" d="M9 1l2.4 5.6 6 .5-4.6 4 1.4 6L9 14l-5.2 3.1 1.4-6-4.6-4 6-.5z"/>
    <use href="#st" x="22"/><use href="#st" x="44"/><use href="#st" x="66"/><use href="#st" x="88"/>
  </svg>
  <p class="abs quote">" Lorem Ipsum has been the industry's standard dummy text ever since the 1500s, when an unknown printer took a galley of type and scrambled it to make a type specimen book. It has survived not only five centuries.."</p>
  <div class="abs client">— Client Name</div>
  <div class="abs dots"><span></span><span></span><span class="on"></span><span></span><span></span></div>
</section>

<section>
  <h2 class="abs contact-title">Contact Us</h2>
  <div class="abs contact-item" style="top:2240px">
    <div class="contact-icon"><svg width="18" height="22" viewBox="0 0 18 22"><path d="M9 21s7-7 7-12A7 7 0 0 0 2 9c0 5 7 12 7 12z" fill="none" stroke="#fff" stroke-width="1.6"/><circle cx="9" cy="9" r="2.5" fill="none" stroke="#fff" stroke-width="1.6"/></svg></div>
    <div>101 - Lorem ipsum sumple text<br>print type industry text.</div>
  </div>
  <div class="abs contact-item" style="top:2305px">
    <div class="contact-icon"><svg width="18" height="18" viewBox="0 0 18 18"><path d="M3 1l4 4-2 2.5c1 2.5 3 4.5 5.5 5.5L13 11l4 4-2.5 2.5C8 17 1 10 .5 3.5z" fill="#fff"/></svg></div>
    <div>Phone :<br>+(1) 555 014 2236</div>
  </div>
  <div class="abs contact-item" style="top:2368px">
    <div class="contact-icon"><svg width="18" height="18" viewBox="0 0 18 18" fill="#fff"><rect x="5" y="1" width="8" height="5"/><rect x="1" y="6" width="16" height="7" rx="1"/><rect x="5" y="11" width="8" height="6" fill="#fff" stroke="var(--navy)"/></svg></div>
    <div>Fax:<br>+(1) 555 014 2237</div>
  </div>
  <div class="abs map" role="img" aria-label="Street map showing the practice location"></div>
  <div class="abs map-edge"></div>
</section>

<footer class="abs site-footer">
  <div class="abs footer-brand">Valmora Health</div>
  <div class="abs social" style="left:1020px" aria-label="Social link"></div>
  <div class="abs social" style="left:1061px" aria-label="Social link"></div>
  <div class="abs social" style="left:1103px" aria-label="Social link"></div>
  <div class="abs footer-links"><span>Home</span>|<span>About Us</span>|<span>Services</span>|<span>Employers</span>|<span>Blog</span>|<span>Contact Us</span></div>
  <div class="abs footer-copy">©ValmoraHealth- 2021 All rights reserved.</div>
</footer>

</body>
</html>
```